New Innovative Counselling and psychotherapy Service needs Business Card design

Keep it simple and professional. On one side, just company name and logo (perhaps in all blue) and maybe a tag line.

On other side (all white) my name and Qualifications in centre

Industry/Entity Type

Health And Wellness

Contact Information for Business Card

Dara Whelby
Counsellor & Psychotherapist
BSc (Psychol.), BA, Dip. (Couns. & Psych.), PG.Cert (CBT), FGTrK, ONRE

I will also require Mobile no, Email and web site address of which I'll pass on to final designer.

Font styles to use
Sans Serif

Requirements
Must have
• My Logo Only and please use the colours in logo that is in it.
Should not have
• Any other images

```html
<!DOCTYPE html>
<html lang="en">
<head>
<meta charset="utf-8">
<title>Kindred Lane – Business Card</title>
<link rel="stylesheet" href="https://fonts.googleapis.com/css2?family=Open+Sans:wght@400;600;700&display=swap">
<style>
  :root {
    --backdrop: #3a3330;
    --card: #141516;
    --brand-blue: #3a9fd8;
    --brand-green: #7cc242;
    --text-white: #f2f2f2;
    --text-grey: #9a9a9a;
    --divider: #5a5a5a;
  }
  * { box-sizing: border-box; margin: 0; padding: 0; }
  html, body { width: 1200px; height: 864px; overflow: hidden; }
  body {
    background: var(--backdrop);
    font-family: "Open Sans", Arial, sans-serif;
    position: relative;
  }
  .card {
    position: absolute;
    width: 560px;
    height: 320px;
    background: var(--card);
    border-radius: 4px;
    box-shadow: 0 10px 28px rgba(0,0,0,0.45);
  }
  .card-front { left: 50px; top: 60px; }
  .card-back { left: 590px; top: 484px; }

  /* Front */
  .front-brand {
    position: absolute;
    top: 96px; left: 0; right: 0;
    display: flex; align-items: center; justify-content: center; gap: 16px;
  }
  .front-brand .mark-dot {
    width: 44px; height: 44px; border-radius: 50%;
    background: var(--brand-blue);
  }
  .front-brand .brand-name {
    font-size: 40px; font-weight: 600; color: var(--brand-blue); letter-spacing: 0.5px;
  }
  .tagline {
    position: absolute; left: 0; right: 0; bottom: 70px;
    text-align: center; font-size: 14px; font-style: italic; color: var(--text-grey);
  }

  /* Back */
  .back-brand {
    position: absolute; left: 36px; top: 142px;
    display: flex; align-items: center; gap: 10px;
  }
  .back-brand .mark-dot {
    width: 24px; height: 24px; border-radius: 50%; background: var(--brand-blue);
  }
  .back-brand .brand-name {
    font-size: 21px; font-weight: 400; color: var(--text-white);
  }
  .back-divider {
    position: absolute; left: 232px; top: 70px; width: 1px; height: 180px;
    background: var(--divider);
  }
  .details { position: absolute; left: 252px; top: 76px; right: 20px; }
  .person-name {
    font-size: 19px; font-weight: 700; color: var(--brand-blue); text-transform: uppercase; line-height: 1.1;
  }
  .person-role {
    font-size: 15.5px; font-weight: 600; color: var(--brand-green); text-transform: uppercase; line-height: 1.3;
  }
  .qualifications {
    font-size: 11px; color: var(--brand-green); line-height: 1.35; margin-top: 2px;
  }
  .contact-list { list-style: none; margin-top: 10px; }
  .contact-list li {
    display: flex; align-items: center; gap: 10px;
    font-size: 14.5px; color: var(--text-white); line-height: 1.55;
  }
  .contact-list svg { width: 13px; height: 13px; flex: none; }
</style>
</head>
<body>
  <section class="card card-front">
    <div class="front-brand">
      <span class="mark-dot"></span>
      <span class="brand-name">Kindred Lane</span>
    </div>
    <p class="tagline">Caring For Your Psychological Well-Being Is Our Top Priority</p>
  </section>

  <section class="card card-back">
    <div class="back-brand">
      <span class="mark-dot"></span>
      <span class="brand-name">Kindred Lane</span>
    </div>
    <div class="back-divider"></div>
    <div class="details">
      <h1 class="person-name">Dara Whelby</h1>
      <p class="person-role">Counsellor &amp; Psychotherapist</p>
      <p class="qualifications">BSc (Psychol.), BA, Dip. (Couns. &amp; Psych.)<br>PG.Cert (CBT), FGTrK,</p>
      <ul class="contact-list">
        <li>
          <svg viewBox="0 0 13 13" aria-hidden="true"><rect x="3" y="0.5" width="7" height="12" rx="1.2" fill="none" stroke="#3a9fd8" stroke-width="1.3"/><rect x="5" y="10" width="3" height="1" fill="#3a9fd8"/></svg>
          555 210 4187
        </li>
        <li>
          <svg viewBox="0 0 13 13" aria-hidden="true"><rect x="0.7" y="2.5" width="11.6" height="8" fill="none" stroke="#3a9fd8" stroke-width="1.3"/><path d="M0.7 2.5 L6.5 7 L12.3 2.5" fill="none" stroke="#3a9fd8" stroke-width="1.3"/></svg>
          dara@kindredlane.com
        </li>
        <li>
          <svg viewBox="0 0 13 13" aria-hidden="true"><circle cx="6.5" cy="6.5" r="6" fill="#3a9fd8"/><ellipse cx="6.5" cy="6.5" rx="2.4" ry="6" fill="none" stroke="#141516" stroke-width="0.9"/><line x1="0.5" y1="6.5" x2="12.5" y2="6.5" stroke="#141516" stroke-width="0.9"/></svg>
          www.kindredlane.com
        </li>
      </ul>
    </div>
  </section>
</body>
</html>
```